Meadowlark Property Review is a leading provider of residential appraisal and home inspection products in S

I need a business card/logo designed that obviously describes my business. We are a residential appraisal and home inspection company in Springfield, MO. We offer residential appraisals, home inspection, pest inspection and radon gas measurement. We have been in business for 18 years and hold state certified residential appraisal licenses and OBREX certified home inspection licenses. I have a logo that I really like and will attach, but would be open to new suggestions. I like more modern designs than traditional and would like a two sided card with our services, licenses and qualifications on the back.

```html
<!DOCTYPE html>
<html lang="en">
<head>
<meta charset="utf-8">
<title>Meadowlark Property Review — Business Card</title>
<link href="https://fonts.googleapis.com/css2?family=Source+Sans+3:ital,wght@0,400;0,600;1,400&display=swap" rel="stylesheet">
<style>
  :root {
    --backdrop: #3a3a3a;
    --card-white: #f7f7f7;
    --panel-brown: #8c6a43;
    --accent-orange: #f08a1c;
    --logo-brown: #8a6a44;
    --text-light: #ffffff;
    --text-dark: #4a4a4a;
    --text-muted: #7a7a7a;
  }
  * { margin: 0; padding: 0; box-sizing: border-box; }
  html, body {
    width: 1200px; height: 750px; overflow: hidden;
    background: var(--backdrop);
    font-family: "Source Sans 3", sans-serif;
  }
  .card {
    position: absolute; top: 228px;
    width: 462px; height: 263px;
    background: var(--card-white);
  }
  .card-front { left: 124px; }
  .card-back { left: 618px; }

  .contact-panel {
    position: absolute; left: 0; top: 0;
    width: 222px; height: 100%;
    background: var(--panel-brown);
    border-right: 2px solid var(--accent-orange);
    color: var(--text-light);
    padding: 50px 0 0 38px;
  }
  .person-name {
    color: var(--accent-orange);
    font-size: 17px; font-weight: 600; line-height: 1.1;
  }
  .person-title { font-size: 13px; margin-top: 2px; }
  .address { font-size: 11px; line-height: 14px; margin-top: 17px; }
  .contact-list { list-style: none; margin-top: 9px; }
  .contact-list li {
    display: flex; align-items: center; gap: 6px;
    font-size: 11px; height: 17.5px;
  }
  .contact-list svg { width: 12px; height: 12px; flex: none; fill: var(--accent-orange); }

  .brand-area {
    position: absolute; left: 224px; right: 0; top: 0; bottom: 0;
    display: flex; align-items: center; justify-content: center;
    padding: 0 24px;
  }
  .brand-name {
    color: var(--logo-brown);
    font-size: 20px; font-weight: 600; line-height: 1.15;
    display: flex; align-items: center; gap: 9px;
  }
  .brand-dot { width: 10px; height: 10px; border-radius: 50%; background: var(--accent-orange); flex: none; }

  .back-brand {
    position: absolute; left: 0; right: 0; top: 84px;
    display: flex; justify-content: center;
  }
  .back-brand .brand-name { font-size: 24px; }
  .back-brand .brand-dot { width: 12px; height: 12px; }
  .services {
    position: absolute; left: 0; right: 0; top: 180px;
    text-align: center; color: var(--text-dark);
    font-size: 12px; font-style: italic; line-height: 18px;
  }
  .services .sep { color: var(--accent-orange); font-style: normal; }
  .credentials {
    position: absolute; left: 0; right: 0; top: 224px;
    text-align: center; color: var(--text-muted);
    font-size: 10px; line-height: 13px;
  }
  .credentials .sep { color: var(--accent-orange); }
</style>
</head>
<body>
  <section class="card card-front">
    <div class="contact-panel">
      <div class="person-name">Daniel Reyes</div>
      <div class="person-title">CEO/Founder</div>
      <div class="address">2418 Larkspur Court<br>Springfield, Missouri 65804</div>
      <ul class="contact-list">
        <li><svg viewBox="0 0 12 12" aria-hidden="true"><path d="M2.5 1 L4.5 1 L5.2 3.6 L4 4.6 Q5 7 7.4 8 L8.4 6.8 L11 7.5 L11 9.5 Q10.5 11 9 11 Q1 10 1 3 Q1 1.5 2.5 1Z"/></svg>417 555 0186</li>
        <li><svg viewBox="0 0 12 12" aria-hidden="true"><rect x="3" y="1" width="6" height="3"/><rect x="0.5" y="4.5" width="11" height="5" rx="1"/><rect x="3" y="8" width="6" height="3"/></svg>417 555 0247</li>
        <li><svg viewBox="0 0 12 12" aria-hidden="true"><rect x="0.5" y="2.5" width="11" height="7"/><path d="M0.5 2.5 L6 7 L11.5 2.5" fill="none" stroke="#8c6a43" stroke-width="1"/></svg>dan@meadowlarkreview.com</li>
        <li><svg viewBox="0 0 12 12" aria-hidden="true"><circle cx="6" cy="6" r="5.5"/><path d="M0.5 6 H11.5 M6 0.5 V11.5 M6 0.5 Q2.5 6 6 11.5 M6 0.5 Q9.5 6 6 11.5" fill="none" stroke="#8c6a43" stroke-width="0.8"/></svg>www.meadowlarkreview.com</li>
      </ul>
    </div>
    <div class="brand-area">
      <div class="brand-name"><span class="brand-dot"></span><span>Meadowlark<br>Property Review</span></div>
    </div>
  </section>

  <section class="card card-back">
    <div class="back-brand">
      <div class="brand-name"><span class="brand-dot"></span>Meadowlark Property Review</div>
    </div>
    <p class="services">
      Residential appraisals <span class="sep">•</span> Home inspection<br>
      Pest inspection and radon gas measurement.
    </p>
    <p class="credentials">
      State Certified Residential Appraiser <span class="sep">•</span> OBREX Certified Home Inspector<br>
      Serving Springfield, MO for 18 years
    </p>
  </section>
</body>
</html>
```